Specialised investor in e-mobility and energy wants business card design

We need a business card design that fits our existing corporate design. <The look and feel must be 'sharp'/'clean', dynamic, communicate momentum, professionalism etc (as one would imagine from a firm in the financial sector). We like the idea of a reverse-side of the card that includes the logo, and the name and contact details on the other. We expect the deliverable to be whatever format might be required to be able to get cards printed directly by a service such as kelmo press. Our website is www.zub.capital

```html
<!DOCTYPE html>
<html lang="en">
<head>
<meta charset="utf-8">
<title>ZUB Capital – Business Card</title>
<link rel="stylesheet" href="https://fonts.googleapis.com/css2?family=Arimo:wght@400;700&display=swap">
<style>
  :root {
    --backdrop: #141614;
    --card-dark: #22401a;
    --card-mid: #2d4d22;
    --card-edge: #6aa536;
    --accent: #74b13a;
    --pattern-dark: #1f3a17;
    --pattern-light: #2f5724;
    --ink: #ffffff;
  }
  * { box-sizing: border-box; margin: 0; padding: 0; }
  html, body {
    width: 1200px; height: 963px; overflow: hidden;
    background: var(--backdrop);
    font-family: "Arimo", Arial, sans-serif;
    color: var(--ink);
  }
  .sheet {
    width: 1200px; height: 963px;
    display: flex; flex-direction: column; align-items: center; justify-content: center;
    gap: 40px;
  }
  .card {
    position: relative;
    width: 680px; height: 400px;
    border-radius: 26px;
    overflow: hidden;
    background: linear-gradient(135deg, var(--card-dark) 0%, var(--card-mid) 55%, var(--card-dark) 100%);
    box-shadow: 0 3px 0 var(--card-edge), 0 18px 40px rgba(0,0,0,.55);
  }
  .brand {
    position: absolute;
    display: flex; align-items: center; gap: 12px;
    font-weight: 400; color: var(--ink); letter-spacing: .5px;
  }
  .brand-dot {
    width: 16px; height: 16px; border-radius: 50%;
    background: var(--accent);
  }
  /* front */
  .card-front .brand { right: 52px; top: 120px; font-size: 50px; }
  .holder {
    position: absolute; left: 44px; top: 218px;
    font-weight: 700; font-size: 19px; letter-spacing: .5px;
  }
  .holder .surname { color: var(--accent); }
  .rule {
    position: absolute; left: 40px; top: 248px;
    width: 520px; height: 1.5px; background: var(--ink);
  }
  .contacts {
    position: absolute; left: 44px; top: 266px;
    list-style: none; font-size: 17px; line-height: 30px;
  }
  .contacts li { display: flex; align-items: center; gap: 12px; }
  .contacts svg { width: 16px; height: 16px; flex: none; }
  .location {
    position: absolute; right: 124px; top: 270px;
    text-align: right; font-size: 18px; line-height: 26px;
  }
  /* back */
  .pattern {
    position: absolute; inset: 0;
    background:
      radial-gradient(circle at 30% 30%, var(--pattern-light) 0%, transparent 55%),
      radial-gradient(circle at 80% 75%, var(--pattern-light) 0%, transparent 50%),
      var(--pattern-dark);
  }
  .card-back .brand { right: 70px; top: 160px; font-size: 52px; }
</style>
</head>
<body>
<main class="sheet">
  <section class="card card-front" aria-label="Card front">
    <div class="brand"><span class="brand-dot"></span>ZUB Capital</div>
    <p class="holder">MARTEN <span class="surname">SOLBERG</span></p>
    <div class="rule"></div>
    <ul class="contacts">
      <li>
        <svg viewBox="0 0 16 16" aria-hidden="true"><path fill="var(--accent)" d="M3.5 1.5l2.5 0 1 3.5-1.7 1.2a9 9 0 0 0 4.5 4.5L11 9l3.5 1v2.5a2 2 0 0 1-2 2A11 11 0 0 1 1.5 3.5a2 2 0 0 1 2-2z"/></svg>
        +41 79 555 0148
      </li>
      <li>
        <svg viewBox="0 0 16 16" aria-hidden="true"><rect x="1" y="3" width="14" height="10" rx="1" fill="var(--accent)"/><path d="M1.5 3.8L8 9l6.5-5.2" fill="none" stroke="var(--card-dark)" stroke-width="1.3"/></svg>
        marten@zub.capital
      </li>
      <li>
        <svg viewBox="0 0 16 16" aria-hidden="true"><circle cx="8" cy="8" r="7" fill="var(--accent)"/><path d="M1 8h14M8 1c-3 3.5-3 10.5 0 14M8 1c3 3.5 3 10.5 0 14" fill="none" stroke="var(--card-dark)" stroke-width="1"/></svg>
        www.zub.capital
      </li>
    </ul>
    <p class="location">Geneva<br>Switzerland</p>
  </section>

  <section class="card card-back" aria-label="Card back">
    <div class="pattern" role="img" aria-label="Repeating embossed brand-mark pattern in dark and light green"></div>
    <div class="brand"><span class="brand-dot"></span>ZUB Capital</div>
  </section>
</main>
</body>
</html>
```